Classy, Elegant, Simple Business Card Design

Looking to have a classy, simple, and elegant design. Want a top notch designed business card. I really like the look of the new torvane credit card. I also like the design I attached. I am trying to reach 21-29 year old females for booking us for there wedding or event. We offer Disc Jockey Service, Photo Booth Rentals, and Uplighting .

Target Market(s)

21-28 year old females

Contact Information for Business Card

Has to have logo, website, email, and phone number

Font styles to use
Other font styles liked:
• open to font choice, modern, clean
Designer to choose
33a6d7
0791cd
0555a3
ffffff

Requirements
Must have
• Has to have logo, website, email, and phone number
Nice to have
• I really like the design of the new torvane credit card. I also included my logo and some designs I like
Should not have
• clutter or too much info

```html
<!DOCTYPE html>
<html lang="en">
<head>
<meta charset="utf-8">
<title>Lumen Tide Event Group – Business Card</title>
<link rel="stylesheet" href="https://fonts.googleapis.com/css2?family=Jost:wght@400;500&family=Roboto:wght@400;700&display=swap">
<style>
  :root {
    --backdrop: #3b3b3d;
    --card-black: #1c1c1f;
    --card-blue: #0f5fa8;
    --accent-blue: #1f8ad6;
    --silver: #a9abb0;
    --divider-grey: #b7b9bd;
    --white: #ffffff;
  }
  html, body {
    margin: 0;
    padding: 0;
    width: 799px;
    height: 1200px;
    overflow: hidden;
    background: var(--backdrop);
  }
  .canvas {
    position: relative;
    width: 799px;
    height: 1200px;
  }
  .card {
    position: absolute;
    left: 85px;
    width: 630px;
    height: 360px;
    border-radius: 4px;
    overflow: hidden;
    background: var(--card-black);
    box-shadow: 0 14px 30px rgba(0,0,0,0.45);
  }
  .card--front { top: 150px; }
  .card--back { top: 690px; }

  .brand {
    position: absolute;
    font-family: "Jost", sans-serif;
    font-weight: 400;
    letter-spacing: 0.14em;
    text-transform: uppercase;
    line-height: 1.15;
    display: flex;
    align-items: center;
    gap: 14px;
  }
  .brand__mark {
    width: 14px;
    height: 14px;
    border-radius: 50%;
    flex: none;
  }
  .brand__name { display: block; }
  .brand__sub { display: block; font-size: 0.5em; letter-spacing: 0.45em; }

  .card--front .brand {
    left: 0; right: 0; top: 0; bottom: 0;
    justify-content: center;
    color: var(--silver);
    font-size: 40px;
  }
  .card--front .brand__mark { background: var(--silver); }

  .card--back .shape { position: absolute; inset: 0; }
  .card--back .brand {
    left: 40px;
    top: 130px;
    color: var(--accent-blue);
    font-size: 27px;
  }
  .card--back .brand__mark { background: var(--accent-blue); width: 11px; height: 11px; }

  .contact {
    position: absolute;
    left: 365px;
    top: 118px;
    color: var(--white);
    font-family: "Roboto", sans-serif;
  }
  .contact__name { margin: 0; font-size: 25px; font-weight: 700; }
  .contact__role { margin: 2px 0 16px; font-size: 15px; font-weight: 400; }
  .contact__list { list-style: none; margin: 0; padding: 0; font-size: 16px; }
  .contact__item { display: flex; align-items: center; gap: 10px; margin-bottom: 6px; }
  .contact__icon { width: 14px; height: 14px; flex: none; }
</style>
</head>
<body>
<main class="canvas">
  <section class="card card--front" aria-label="Card front">
    <div class="brand">
      <span class="brand__mark"></span>
      <span><span class="brand__name">Lumen Tide</span><span class="brand__sub">Event Group</span></span>
    </div>
  </section>

  <section class="card card--back" aria-label="Card back">
    <svg class="shape" viewBox="0 0 630 360" preserveAspectRatio="none" aria-hidden="true">
      <path d="M330 0 C 280 110 270 250 220 360 L630 360 L630 0 Z" fill="var(--divider-grey)"/>
      <path d="M345 0 C 295 110 287 250 238 360 L630 360 L630 0 Z" fill="var(--card-blue)"/>
    </svg>
    <div class="brand">
      <span class="brand__mark"></span>
      <span><span class="brand__name">Lumen Tide</span><span class="brand__sub">Event Group</span></span>
    </div>
    <div class="contact">
      <h1 class="contact__name">Ellis Marlow</h1>
      <p class="contact__role">Founder &amp; CEO</p>
      <ul class="contact__list">
        <li class="contact__item">
          <svg class="contact__icon" viewBox="0 0 16 16" aria-hidden="true"><path d="M3 2h3l1 4-2 1c1 2 2 3 4 4l1-2 4 1v3c0 1-1 1-1 1C7 14 2 9 2 3c0 0 0-1 1-1z" fill="var(--white)"/></svg>
          <span>555 0142 0199</span>
        </li>
        <li class="contact__item">
          <svg class="contact__icon" viewBox="0 0 16 16" aria-hidden="true"><rect x="1" y="3" width="14" height="10" fill="none" stroke="var(--white)" stroke-width="1.5"/><path d="M1 3l7 6 7-6" fill="none" stroke="var(--white)" stroke-width="1.5"/></svg>
          <span>ellis@lumentide.com</span>
        </li>
        <li class="contact__item">
          <svg class="contact__icon" viewBox="0 0 16 16" aria-hidden="true"><circle cx="8" cy="8" r="6.5" fill="none" stroke="var(--white)" stroke-width="1.4"/><path d="M1.5 8h13M8 1.5c-3 3.5-3 9.5 0 13M8 1.5c3 3.5 3 9.5 0 13" fill="none" stroke="var(--white)" stroke-width="1.2"/></svg>
          <span>www.lumentide.com</span>
        </li>
      </ul>
    </div>
  </section>
</main>
</body>
</html>
```